Creative, fresh business card design for Ripplecraft Facades

We need a fresh, creative business card design for Ripplecraft Facades. We are the manufacturer of Ripplecraft Facades in Australia. Wall panels are 2400 x 1200mm panels made from MDF and feature 3D patterns on the face of the panel. The colours to be used are green, silver/grey and white RGB
Red 187
Green 207
Blue 65.

An idea is to possibly use a watermark of one of our designs as a background (like on the "Grids" design on the left hand side of page 2 of our brochure).

Target Market(s)

Interior designers, architects, builders and home renovators

Industry/Entity Type

Business

Contact Information for Business Card

Details to go on the card are:
Our logo (attached),
Slogan: "Decorative panels for interiors and exteriors",
Contact name,
Position,
Mobile phone number,
Business address,
Business phone,
Business fax,
Website and
Email address.

I have attached a few images of our panels and our brochure for reference.

The colours of the business card should feature our logo colours which are: RGB
Red 187
Green 207
Blue 65

Requirements
Must have
• Very modern fonts and design. Some of the designs shown especially the "Prisms" design which is a popular design.
Nice to have
• Creative but simple design. Very contemporary.
Should not have
• Anything ornate or old fashioned.

```html
<!DOCTYPE html>
<html lang="en">
<head>
<meta charset="utf-8">
<title>Ripplecraft Facades – Business Card</title>
<link rel="stylesheet" href="https://fonts.googleapis.com/css2?family=Open+Sans:wght@400;600;700&display=swap">
<style>
  :root {
    --stage: #2e2a28;
    --card: #0f0f10;
    --card-edge: #1a1a1b;
    --lime: #bbcf41;
    --silver: #a7a9ac;
    --white: #f2f2f2;
  }
  * { box-sizing: border-box; margin: 0; padding: 0; }
  html, body { width: 1200px; height: 844px; overflow: hidden; }
  body {
    background: var(--stage);
    font-family: "Open Sans", Arial, sans-serif;
    position: relative;
  }
  .card {
    position: absolute;
    width: 540px;
    height: 309px;
    background: var(--card);
    border: 1px solid var(--card-edge);
    box-shadow: 0 18px 40px rgba(0,0,0,.45);
    overflow: hidden;
  }
  .card--front { left: 40px; top: 268px; }
  .card--back { left: 620px; top: 268px; }

  .brand { display: flex; align-items: center; gap: 10px; }
  .brand__square { width: 22px; height: 22px; background: var(--lime); flex: none; }
  .brand__name { font-weight: 700; color: var(--white); white-space: nowrap; }

  .card--front .brand { position: absolute; left: 150px; top: 62px; }
  .card--front .brand__name { font-size: 20px; }

  .contact {
    position: absolute; right: 24px; top: 56px;
    list-style: none; text-align: right;
  }
  .contact__item {
    display: flex; justify-content: flex-end; align-items: center; gap: 8px;
    color: var(--white); font-size: 12.5px; line-height: 23px;
  }
  .contact__icon { width: 11px; height: 11px; fill: var(--lime); flex: none; }

  .person { position: absolute; left: 28px; top: 178px; }
  .person__name { color: var(--lime); font-weight: 700; font-size: 17px; line-height: 20px; }
  .person__role { color: var(--white); font-size: 12.5px; line-height: 17px; }
  .address { position: absolute; left: 28px; top: 248px; color: var(--white); font-size: 12.5px; line-height: 17px; }

  .card__texture {
    position: absolute; inset: 0;
    background: linear-gradient(115deg, #0c0c0d 0%, #1e1e20 30%, #0e0e0f 50%, #202022 70%, #0c0c0d 100%);
    opacity: .9;
  }
  .card--back .brand { position: absolute; left: 150px; top: 100px; }
  .card--back .brand__square { width: 30px; height: 30px; }
  .card--back .brand__name { font-size: 26px; }
  .slogan {
    position: absolute; left: 190px; top: 146px;
    color: var(--silver); font-size: 12px; letter-spacing: 2px; line-height: 16px;
  }
</style>
</head>
<body>
  <section class="card card--front" aria-label="Business card front">
    <div class="brand">
      <span class="brand__square"></span>
      <span class="brand__name">Ripplecraft Facades</span>
    </div>

    <ul class="contact">
      <li class="contact__item">0412-555-019
        <svg class="contact__icon" viewBox="0 0 12 12"><rect x="3" y="0" width="6" height="12" rx="1"/></svg></li>
      <li class="contact__item">(03)-5550-7821
        <svg class="contact__icon" viewBox="0 0 12 12"><path d="M2 1l3 0 1 3-2 1a7 7 0 0 0 3 3l1-2 3 1 0 3c-6 1-10-3-9-9z"/></svg></li>
      <li class="contact__item">(03)-5550-7822
        <svg class="contact__icon" viewBox="0 0 12 12"><rect x="1" y="4" width="10" height="7"/><rect x="3" y="0" width="6" height="4"/></svg></li>
      <li class="contact__item">info@ripplecraft.example
        <svg class="contact__icon" viewBox="0 0 12 12"><path d="M0 2h12v8H0z M0 2l6 5 6-5" /></svg></li>
      <li class="contact__item">www.ripplecraft.example
        <svg class="contact__icon" viewBox="0 0 12 12"><circle cx="6" cy="6" r="6"/></svg></li>
    </ul>

    <div class="person">
      <p class="person__name">Marcus Hale</p>
      <p class="person__role">Managing Director</p>
    </div>
    <p class="address">48 Kiln Street, Geelong<br>Australia, 3220</p>
  </section>

  <section class="card card--back" aria-label="Business card back">
    <div class="card__texture" role="img" aria-label="Faint wave-pattern panel texture in dark greys"></div>
    <div class="brand">
      <span class="brand__square"></span>
      <span class="brand__name">Ripplecraft Facades</span>
    </div>
    <p class="slogan">decorative panels for<br>interiors &amp; landscapes</p>
  </section>
</body>
</html>
```